Upmarket Dessert Lounge needs a Business Card Design

We are an upmarket dessert lounge needing a business card to match our image.

We want something that is simple yet beautiful, feminine, classy, sophisticated and elegant. We want it to stand out and don't mind if it is bold.

The design should include our logo and colours of red or maroon with gold highlights. We don't mind if black is used.

Marlow & Quince

Target Market(s)

For those who like to indulge or treat themselves and give in to their temptations on good quality desserts.

Industry/Entity Type

Business

Requirements
Must have
• Must include our logo and our name

Marlow & Quince

M & Q

```html
<!DOCTYPE html>
<html lang="en">
<head>
<meta charset="utf-8">
<title>Marlow &amp; Quince — Business Card</title>
<link href="https://fonts.googleapis.com/css2?family=Tinos:wght@400;700&display=swap" rel="stylesheet">
<style>
  :root {
    --backdrop: #e8e2dc;
    --card-black: #020202;
    --maroon: #7a1416;
    --gold: #e9c48e;
    --cream: #f5dcb2;
    --white: #ffffff;
    --divider: #c9a9a0;
  }
  html, body {
    margin: 0;
    padding: 0;
    width: 1200px;
    height: 417px;
    overflow: hidden;
    background: var(--backdrop);
    font-family: "Tinos", "Times New Roman", serif;
  }
  .canvas {
    position: relative;
    width: 1200px;
    height: 417px;
  }
  .card {
    position: absolute;
    top: 62px;
    width: 514px;
    height: 293px;
    background: var(--card-black);
    border-radius: 14px;
    overflow: hidden;
    box-shadow: 0 2px 6px rgba(0,0,0,0.35);
  }
  .card--front { left: 56px; }
  .card--back { left: 629px; }

  .contact-band {
    position: absolute;
    top: 0; left: 0; right: 0;
    height: 73px;
    background: var(--maroon);
    border-bottom: 2px solid var(--gold);
    color: var(--white);
    font-size: 13.5px;
    line-height: 19px;
  }
  .contact-group {
    position: absolute;
    top: 24px;
  }
  .contact-group--address { left: 35px; }
  .contact-group--phones { left: 175px; padding-left: 10px; border-left: 1px solid var(--divider); }
  .contact-group--online { left: 321px; padding-left: 12px; border-left: 1px solid var(--divider); }
  .contact-line { display: flex; align-items: center; gap: 6px; white-space: nowrap; }
  .contact-line svg { width: 10px; height: 10px; flex: none; }

  .wordmark {
    position: absolute;
    left: 0; right: 0;
    text-align: center;
    color: var(--cream);
    font-size: 29px;
    font-weight: 400;
    letter-spacing: 1px;
  }
  .card--front .wordmark { top: 152px; }
  .card--back .wordmark { top: 128px; }

  .holder {
    position: absolute;
    left: 0; right: 0;
    top: 259px;
    text-align: center;
    color: var(--gold);
    font-size: 18px;
    font-weight: 700;
  }
  .holder .holder-title { font-size: 14px; font-weight: 400; }

  .back-url {
    position: absolute;
    left: 0; right: 0;
    top: 251px;
    text-align: center;
    color: var(--white);
    font-size: 13px;
    letter-spacing: 2.6px;
  }
</style>
</head>
<body>
<main class="canvas">
  <section class="card card--front" aria-label="Business card front">
    <header class="contact-band">
      <div class="contact-group contact-group--address">
        <div class="contact-line">00, Complex name</div>
        <div class="contact-line">City, State 000 000</div>
      </div>
      <div class="contact-group contact-group--phones">
        <div class="contact-line">
          <svg viewBox="0 0 10 10" aria-hidden="true"><path d="M2 1 L4 1 L4.6 3 L3.4 4 Q4.5 6 6 6.6 L7 5.4 L9 6 L9 8 Q8 9.5 6 8.6 Q2.5 7 1 3.5 Q0.7 1.8 2 1 Z" fill="#fff"/></svg>
          +2348100456712
        </div>
        <div class="contact-line">
          <svg viewBox="0 0 10 10" aria-hidden="true"><rect x="2.5" y="0.5" width="5" height="9" rx="1" fill="#fff"/><rect x="3.4" y="1.6" width="3.2" height="5" fill="#7a1416"/></svg>
          +2348100456712
        </div>
      </div>
      <div class="contact-group contact-group--online">
        <div class="contact-line">
          <svg viewBox="0 0 10 10" aria-hidden="true"><rect x="0.5" y="2" width="9" height="6" fill="#fff"/><path d="M0.5 2 L5 5.5 L9.5 2" stroke="#7a1416" stroke-width="0.8" fill="none"/></svg>
          hello@marlowquince.com
        </div>
        <div class="contact-line">
          <svg viewBox="0 0 10 10" aria-hidden="true"><circle cx="5" cy="5" r="4.3" fill="#fff"/><path d="M0.7 5 H9.3 M5 0.7 Q2.5 5 5 9.3 M5 0.7 Q7.5 5 5 9.3" stroke="#7a1416" stroke-width="0.7" fill="none"/></svg>
          www.marlowquince.com
        </div>
      </div>
    </header>
    <div class="wordmark">MARLOW &amp; QUINCE</div>
    <div class="holder">YOUR NAME / <span class="holder-title">Title</span></div>
  </section>

  <section class="card card--back" aria-label="Business card back">
    <div class="wordmark">MARLOW &amp; QUINCE</div>
    <div class="back-url">www.marlowquince.com</div>
  </section>
</main>
</body>
</html>
```